Stationery Design Project

Our company is "Meridian Systems" and we have a product called "lunogrid.com". The product is an online accounting software for businesses. We want to communicate that our software will help business owners to be more efficient and help them track their finances better. Lunogrid.com is basically a simple version of ledgerpal.

"We want a unique and creative design which will surprise our customer."

NAME CARD = LUNOGRID
We want a lunogrid name card NOT MERIDIAN SYSTEMS.

For the content of the name card, please make sure it fit with a long name like the following:

Rudi Wahyo Alias Rudi
Developer Specialist
T: (021) 4827 1036
F: (021) 4827 1037
E: customer.service@mrdn-sys.example

I need you to put it the following information to the name card

"lunogrid"
- moto is "automate your businesses"
- website "www.lunogrid.com"
- lunogrid is a "Web Accounting Software"
- product of "Meridian Systems"

LETTERHEAD, ENVELOPE, FOLDER = MERIDIAN SYSTEMS
Other than name card we wanted you to design for us; letterhead, envelope and folder. In letterhead, envelope and folder it should ONLY contain the following information ("Meridian Systems").
PLEASE BE SURE YOU ARE NOT PUTTING "LUNOGRID LOGO" IN LETTERHEAD, ENVELOPE AND FOLDER.

"Meridian Systems"
Address:
Ruko Graha Pelangi Blok. D No. 18
Jl. Kenanga Raya No. 71
Jakarta
Cempaka, 11470
Indonesia

Web Address: mrdn-sys.example

T: (021) 4827 1036
F: (021) 4827 1037

Target Market(s)

Business Owners, Accountant, Auditor, Tax Consultant

Industry/Entity Type

Accounting

Requirements

```html
<!DOCTYPE html>
<html lang="en">
<head>
<meta charset="utf-8">
<title>lunogrid name card</title>
<link href="https://fonts.googleapis.com/css2?family=PT+Sans:wght@400;700&display=swap" rel="stylesheet">
<style>
  :root {
    --stage: #a7a7a7;
    --stage-light: #cfcfcf;
    --card-blue-glow: #2fb8e6;
    --card-blue-mid: #1d6db6;
    --card-blue-deep: #174c93;
    --card-white: #f6f8fb;
    --text-white: #ffffff;
    --text-soft: #dfe9f4;
    --text-muted: #a9c0da;
    --title-muted: #9cb3cd;
    --rule: rgba(255,255,255,0.35);
    --brand-grey: #55585c;
    --mark-front: #d7e3ef;
    --mark-back: #6f8fa8;
  }
  * { margin: 0; padding: 0; box-sizing: border-box; }
  html, body { width: 1200px; height: 960px; overflow: hidden; }
  body {
    position: relative;
    background: radial-gradient(ellipse at 50% 40%, var(--stage-light), var(--stage) 75%);
    font-family: "PT Sans", sans-serif;
  }
  .card {
    position: absolute;
    box-shadow: 0 4px 14px rgba(0,0,0,0.35);
    overflow: hidden;
  }
  .card--front {
    left: 271px; top: 61px; width: 695px; height: 411px;
    background: radial-gradient(circle at 353px 179px, var(--card-blue-glow) 0%, var(--card-blue-mid) 40%, var(--card-blue-deep) 85%);
    color: var(--text-white);
  }
  .card--back {
    left: 268px; top: 510px; width: 700px; height: 414px;
    background: radial-gradient(circle at 520px 190px, #ffffff 0%, var(--card-white) 60%, #eef1f5 100%);
  }

  /* product brand, top left */
  .brand {
    position: absolute; left: 43px; top: 30px;
    display: flex; align-items: center; gap: 10px;
  }
  .brand__mark {
    width: 62px; height: 62px; border-radius: 50%;
    background: var(--mark-front);
  }
  .brand__name {
    font-size: 36px; line-height: 40px; font-weight: 400;
    color: var(--text-soft);
  }
  .brand-info {
    position: absolute; left: 114px; top: 86px;
    font-size: 18px; line-height: 20px; color: var(--text-white);
  }

  /* maker block */
  .maker {
    position: absolute; left: 54px; top: 140px;
  }
  .maker__name {
    font-size: 29px; line-height: 32px; color: var(--text-soft); font-weight: 400;
  }
  .maker__kind {
    font-size: 10.5px; letter-spacing: 2px; text-transform: uppercase;
    color: var(--text-soft); margin-top: 1px;
  }
  .maker__line {
    font-size: 19px; line-height: 22px; color: var(--text-white);
  }

  .divider {
    position: absolute; left: 41px; top: 246px; width: 612px; height: 1px;
    background: var(--rule);
  }
  .person {
    position: absolute; right: 43px; top: 214px; text-align: right;
  }
  .person__name { font-size: 28px; font-weight: 700; line-height: 34px; }
  .person__title {
    font-size: 15px; line-height: 20px; letter-spacing: 2px; text-transform: uppercase;
    color: var(--title-muted);
  }
  .address, .contact {
    position: absolute; top: 318px;
    font-size: 19px; line-height: 25px; color: var(--text-muted);
    font-style: normal;
  }
  .address { left: 49px; }
  .contact { right: 43px; text-align: right; }

  .brand--back {
    position: absolute; left: 84px; top: 148px;
    display: flex; align-items: center; gap: 18px;
  }
  .brand--back .brand__mark {
    width: 108px; height: 108px; background: var(--mark-back);
  }
  .brand--back .brand__name {
    font-size: 66px; line-height: 70px; color: var(--brand-grey);
  }
</style>
</head>
<body>
  <section class="card card--front" aria-label="lunogrid name card, front">
    <div class="brand">
      <span class="brand__mark"></span>
      <span class="brand__name">lunogrid</span>
    </div>
    <div class="brand-info">
      <p>automate your businesses</p>
      <p>www.lunogrid.com</p>
    </div>
    <div class="maker">
      <p class="maker__name">Meridian Systems</p>
      <p class="maker__kind">Maker of Web Accounting Software</p>
      <p class="maker__line">Digitize Life</p>
      <p class="maker__line">www.mrdn-sys.example</p>
    </div>
    <div class="divider"></div>
    <div class="person">
      <p class="person__name">Rudi Wahyo Alias Rudi</p>
      <p class="person__title">Developer Specialist</p>
    </div>
    <address class="address">
      Ruko Graha Pelangi Blok. D No. 18<br>
      Jl. Kenanga Raya No. 71 Jakarta<br>
      Cempaka, 11470 Indonesia
    </address>
    <div class="contact">
      <p>T: (021) 4827 1036</p>
      <p>F: (021) 4827 1037</p>
      <p>M: customer.service@mrdn-sys.example</p>
    </div>
  </section>

  <section class="card card--back" aria-label="lunogrid name card, back">
    <div class="brand brand--back">
      <span class="brand__mark"></span>
      <span class="brand__name">lunogrid</span>
    </div>
  </section>
</body>
</html>
```